Etiketten-Design für einen importierten Honig
Zielgruppe
Wir importieren originalen Manuka Honig aus Neuseeland. Der Manuka Honig ist bekannt für seine besonderen Eigenschaften (antibakteriell, etc.). Ein Glas unseres Honigs (500g) kostet zwischen 30 und 150 EUR.
Unsere Zielgruppe sind gesundheitsbewusste Kunden, die wenig preissensibel sind. Überwiegend wird der Manuka Honig im Fachhandel (z.B. Reformhaus, Drogerie, Biomarkt, etc.) verkauft. Der Großteil unserer Kunden ist 30+ Jahre.
Aufgabenstellung
Bei dem Etikett handelt es sich um das erste Produktetikett. Damit ist in der Farbgestaltung noch alles offen. Das Logo und der Name ist jedoch fix.
Das Etikett ist wird auf einem bpa-freien schwarzen Plastikbehälter angebracht. Dieser ist bei Manuka Honigen Standard aufgrund des langen Transports von Neuseeland nach Deutschland (gerne googeln). Der Deckel dieses Behälters ist schwarz.
Nachdem es sich um ein hochpreisiges Produkt handelt, soll das Etikett diese hohe Wertigkeit widerspiegeln. Damit ist eine Veredelung des Etiketts notwendig. Viele Konkurrenten arbeiten mit Gold, alternative Farben sind jedoch auch möglich.
Das Etikett überdeckt drei der vier Seiten des Plastikbehälters (vorne + links + rechts). Die Maße sind 160 mm x 60 mm. Zusätzlich zu den Etikettenmaßen bitte 2 mm Beschnittzugabe je Seite hinzufügen.
Hintergrundinformationen zu unserer Marke:
- Der Markenname lautet Kalvio. Der Markenname leitet sich von der ersten Imkerin Neuseelands ab - Edith Carrow. Sie hatte im Jahr 1839 die ersten Bienenstöcke nach Neuseeland gebracht und den ersten Manuka Honig geerntet.
- Unser Logo ist eine Verbindung einer Frau und den neuseeländischen Farn. Dieses Logo stellt also direkt eine Verbindung zu Neuseeland dar.
- Unsere Marke Kalvio ist eine qualitativ hochwertige, luxuriöse und hochpreisige Marke. Genau wie in dem Logo selbst, sollen diese Verbindungen zu Neuseeland, der Natur (Honig ist ein Naturprodukt) und Edith Carrow auch auf dem Etikett zu finden sein.
Wonach suchen wir:
- Wir sind auf der Suche nach einem einzigartigen Design, der unseren Honig besonders hervorhebt. Das Etikett soll auffällig sein und uns von anderen unterscheiden. (Eye-catching)
- Eine Veredelung des Etiketts ist Pflicht, da dies für uns die Wertigkeit des Etiketts und des Produktes stark erhöht. In welcher Art die Veredelung durchgeführt wird, ist Ihnen überlassen.
Das dürfen Sie frei wählen:
- Bisher haben..

```html
<!DOCTYPE html>
<html lang="de">
<head>
<meta charset="utf-8">
<title>Kalvio Manuka Honig – Etikett</title>
<link href="https://fonts.googleapis.com/css2?family=Montserrat:wght@400;500;600&display=swap" rel="stylesheet">
<style>
  :root {
    --paper: #ffffff;
    --ink: #1a1a1a;
    --black-matt: #000000;
    --black-gloss: #b3b3b3;
    --gold: #f9b233;
    --gold-deep: #c9923a;
    --label-black: #060606;
    --jar-black: #141210;
  }
  * { margin: 0; padding: 0; box-sizing: border-box; }
  html, body { width: 1200px; height: 848px; overflow: hidden; background: var(--paper); }
  body { font-family: "Montserrat", sans-serif; color: var(--ink); }
  .board { position: relative; width: 1200px; height: 848px; }

  .jar-photo {
    position: absolute; left: 72px; top: 86px; width: 304px; height: 536px;
    border-radius: 34px 34px 26px 26px;
    background: linear-gradient(90deg, #0c0b0a 0%, #2a2420 30%, #14110f 60%, #070606 100%);
  }
  .jar-photo__band {
    position: absolute; left: 0; right: 0; top: 230px; height: 310px;
    background: linear-gradient(180deg, rgba(249,178,51,0.55) 0%, rgba(249,178,51,0.12) 12%, rgba(10,9,8,0.9) 30%);
    border-radius: 0 0 26px 26px;
  }
  .jar-lid-photo {
    position: absolute; left: 665px; top: 382px; width: 240px; height: 120px;
    border-radius: 26px 26px 0 0;
    background: linear-gradient(90deg, #0a0a0a 0%, #2b2b2b 35%, #111 70%, #050505 100%);
  }

  .brand-mark {
    position: absolute; left: 20px; top: 600px; width: 260px; height: 220px;
    display: flex; align-items: center; gap: 14px;
  }
  .brand-mark__dot { width: 40px; height: 40px; border-radius: 50%; background: var(--gold-deep); flex: none; }
  .brand-mark__name { font-size: 52px; font-weight: 500; color: var(--gold-deep); letter-spacing: 2px; }

  .swatches { position: absolute; left: 546px; top: 54px; display: flex; gap: 40px; }
  .swatch { width: 126px; text-align: center; }
  .swatch__name { height: 58px; font-size: 17px; line-height: 22px; display: flex; align-items: flex-end; justify-content: center; margin-bottom: 1px; }
  .swatch__chip { height: 38px; }
  .swatch--matt .swatch__chip { background: var(--black-matt); }
  .swatch--gloss .swatch__chip { background: var(--black-gloss); }
  .swatch--gold .swatch__chip { background: var(--gold); }

  .type-sample { position: absolute; left: 500px; top: 208px; width: 546px; text-align: center; }
  .type-sample__alphabet { font-size: 17px; margin-bottom: 4px; }
  .type-sample__text { font-size: 17px; line-height: 21px; white-space: nowrap; }

  .label {
    position: absolute; left: 428px; top: 502px; width: 701px; height: 276px;
    background: var(--label-black); color: var(--gold); overflow: hidden;
  }
  .label__stripe { position: absolute; left: 0; right: 0; top: 19px; height: 10px; background: var(--gold); }
  .label__drips {
    position: absolute; left: 216px; top: 28px; width: 66px; height: 142px;
    background: linear-gradient(180deg, var(--gold) 0%, rgba(249,178,51,0.7) 45%, rgba(249,178,51,0) 100%);
  }
  .label__comb {
    position: absolute;
    background: radial-gradient(circle, rgba(249,178,51,0.14), rgba(249,178,51,0) 70%);
  }
  .label__comb--left { left: 20px; top: 50px; width: 210px; height: 220px; }
  .label__comb--right { left: 490px; top: 50px; width: 210px; height: 220px; }

  .nutrition { position: absolute; left: 56px; top: 80px; width: 132px; font-size: 6.5px; line-height: 9px; }
  .nutrition__title { text-align: center; margin-bottom: 4px; }
  .nutrition__row { display: flex; justify-content: space-between; }
  .nutrition__row--sub { padding-left: 8px; }
  .nutrition__notes { margin-top: 60px; text-align: center; }
  .nutrition__warning { text-transform: uppercase; }

  .weight {
    position: absolute; left: 254px; top: 140px;
    writing-mode: vertical-rl; transform: rotate(180deg);
    font-size: 21px; font-weight: 500; white-space: nowrap;
  }

  .product { position: absolute; left: 296px; top: 58px; width: 110px; text-align: center; }
  .product__mark { width: 84px; height: 84px; border-radius: 50%; border: 4px solid var(--gold); margin: 0 auto 42px; }
  .product__brand { font-size: 17px; font-weight: 500; letter-spacing: 2px; border-bottom: 1px solid var(--gold); padding-bottom: 3px; margin-bottom: 4px; }
  .product__name { font-size: 9px; line-height: 11px; }

  .origin {
    position: absolute; left: 484px; top: 36px;
    writing-mode: vertical-rl; transform: rotate(180deg);
    font-size: 7px; white-space: nowrap;
  }
  .importer { position: absolute; left: 541px; top: 117px; font-size: 7px; line-height: 10px; }
</style>
</head>
<body>
<main class="board">
  <div class="jar-photo" role="img" aria-label="Foto eines schwarzen Honigglases mit Etikett">
    <div class="jar-photo__band"></div>
  </div>
  <div class="jar-lid-photo" role="img" aria-label="Foto des schwarzen Deckels des Honigglases"></div>

  <div class="brand-mark">
    <span class="brand-mark__dot"></span>
    <span class="brand-mark__name">Kalvio</span>
  </div>

  <section class="swatches">
    <div class="swatch swatch--matt"><div class="swatch__name">SCHWARZ<br>MATT</div><div class="swatch__chip"></div></div>
    <div class="swatch swatch--gloss"><div class="swatch__name">SCHWARZ<br>GLANZ</div><div class="swatch__chip"></div></div>
    <div class="swatch swatch--gold"><div class="swatch__name">GOLD</div><div class="swatch__chip"></div></div>
  </section>

  <section class="type-sample">
    <p class="type-sample__alphabet">ABCDEFGHIJKLMNOPQRSTUVWXYZ</p>
    <p class="type-sample__text">Lorem ipsum dolor sit amet, consectetuer adipiscing<br>elit, sed diam nonummy nibh euismod tincidunt ut<br>laoreet dolore magna aliquam erat volutpat. Ut wisi<br>enim ad minim veniam, quis nostrud exerci tation</p>
  </section>

  <section class="label">
    <div class="label__comb label__comb--left" role="img" aria-label="Wabenmuster in Gold"></div>
    <div class="label__comb label__comb--right" role="img" aria-label="Wabenmuster in Gold"></div>
    <div class="label__stripe"></div>
    <div class="label__drips" role="img" aria-label="Herabfließende Honigtropfen in Gold"></div>

    <div class="nutrition">
      <p class="nutrition__title">Nährwertangaben pro 100 g</p>
      <p class="nutrition__row"><span>Energie</span><span>1400 kJ / 329 kcal</span></p>
      <p class="nutrition__row"><span>Fett</span><span>0 g</span></p>
      <p class="nutrition__row nutrition__row--sub"><span>davon gesättigte Fettsäuren</span><span>0 g</span></p>
      <p class="nutrition__row"><span>Kohlenhydrate</span><span>82 g</span></p>
      <p class="nutrition__row nutrition__row--sub"><span>davon Zucker</span><span>80 g</span></p>
      <p class="nutrition__row"><span>Eiweiß</span><span>0,3 g</span></p>
      <p class="nutrition__row"><span>Salz</span><span>0,02 g</span></p>
      <div class="nutrition__notes">
        <p>1 Portion = 10 g</p>
        <p>Trocken, dunkel und<br>nicht über 25 °C lagern</p>
        <p class="nutrition__warning">Honig ist für Säuglinge<br>unter 12 Monaten nicht geeignet</p>
      </div>
    </div>

    <p class="weight">℮ 500g</p>

    <div class="product">
      <div class="product__mark"></div>
      <p class="product__brand">KALVIO</p>
      <p class="product__name">MANUKA HONIG<br>MGO 450+<br>AUS NEUSEELAND</p>
    </div>

    <p class="origin">100% Manuka Honig aus Neuseeland</p>

    <div class="importer">
      <p>Importiert und vertrieben durch:</p>
      <p>Kalvio Handels GmbH</p>
      <p>Lindenweg 12</p>
      <p>80331 München</p>
    </div>
  </section>
</main>
</body>
</html>
```